Start-up braucht modernes/hochwertiges Getränkeetikett
Zielgruppe
Wir sind ein modernes, nachhaltiges Start-up, welches eine neue Getränkekategorie auf den Markt bringt. Ein sogenanntes Elektrolyt-Getränk mit dem Namen FLUXO4. Es ist abgefüllt in eine 500 ml Flasche und enthält Magnesium, Kalzium, Kalium, und Natrium. Diese Stoffe (Elektrolyte) dienen der körperlichen Hydrierung. Zu Dehydrierung kann es durch Hitze, Alkohol, Sport oder Krankheit kommen. Krankheit liegt bei uns allerdings nicht im Fokus. In unserer Zielgruppe befinden sich hauptsächlich Personen im Alter von 18 - 29 Jahren.
Die Geschmacksrichtung ist Zitrone-Limette.
Aufgabenstellung
Das Etikett soll:
- MODERN, SCHLICHT und HOCHWERTIG sein, so dass es im Supermarkt hervorsticht
- erkenntlich machen, dass die Stoffe Magnesium, Natrium, Kalzium und Kalium enthalten sind
- sich farblich deutlich von der Farbe des Inhalts (weiß) abheben. (Vorzugsweise mit einem hellen Blau, türkis)
- für unsere junge Zielgruppe ansprechend sein
- ebenfalls auf die Geschmacksrichtung (Zitrone-Limette) hinweisen, und zwar so, dass wenn man eine weitere Geschmacksrichtung auf den Markt bringen möchte, diese leicht angepasst werden kann.
- nicht nach einem Energydrink oder einem typischen Sportgetränk aussehen
- unter dem Namen den Slogan 'Elektrolyt-Getränk' stehen haben
-Das Etikett ist nicht dursichtig sondern besteht aus Papier
Der Name sowie das Logo können selbstverständlich farblich verändert werden. Bei dem Logo können auch größere Änderungen vollzogen werden.
Bitte beachten Sie die unten zu stehenden Regler um sich einen guten Überblick über unsere Vorstellungen zu verschaffen. Die Platzierung des EAN-Code ist für ihr Design irrelevat .
Bei Unklarheiten gerne nachfragen!

```html
<!DOCTYPE html>
<html lang="de">
<head>
<meta charset="utf-8">
<title>FLUXO4 Elektrolyt-Getränk Etikett</title>
<link rel="stylesheet" href="https://fonts.googleapis.com/css2?family=Montserrat:wght@700&family=Quicksand:wght@300;400&display=swap">
<style>
  :root {
    --backdrop: #e4e5e7;
    --label-edge-left: #b0b5bb;
    --label-mid-left: #8e979e;
    --label-core: #4c5b64;
    --label-mid-right: #75818a;
    --label-edge-right: #9aa1a7;
    --ink-light: #f1f2f3;
    --ink-soft: #e3e6e8;
  }
  * { margin: 0; padding: 0; box-sizing: border-box; }
  html, body {
    width: 667px;
    height: 1200px;
    overflow: hidden;
  }
  body {
    background: var(--backdrop);
    position: relative;
    font-family: "Quicksand", sans-serif;
  }
  .label {
    position: absolute;
    left: 24px;
    top: 86px;
    width: 619px;
    height: 1028px;
    background: linear-gradient(90deg,
      var(--label-edge-left) 0%,
      var(--label-mid-left) 22%,
      var(--label-core) 52%,
      var(--label-mid-right) 78%,
      var(--label-edge-right) 100%);
  }
  .minerals {
    position: absolute;
    top: 24px;
    left: 0;
    width: 100%;
    text-align: center;
    list-style: none;
    color: var(--ink-soft);
    font-weight: 300;
    font-size: 23px;
    line-height: 29px;
    letter-spacing: 0.3px;
  }
  .emblem-ring {
    position: absolute;
    left: 85px;
    top: 209px;
    width: 450px;
    height: 450px;
  }
  .brand {
    position: absolute;
    left: 0;
    width: 100%;
    text-align: center;
    color: var(--ink-light);
  }
  .brand-name {
    top: 798px;
    font-family: "Montserrat", sans-serif;
    font-weight: 700;
    font-size: 43px;
    line-height: 50px;
    letter-spacing: 1px;
  }
  .brand-tagline {
    top: 856px;
    font-weight: 300;
    font-size: 32px;
    line-height: 38px;
  }
  .brand-flavour {
    top: 910px;
    font-weight: 400;
    font-size: 21px;
    line-height: 28px;
  }
</style>
</head>
<body>
  <section class="label">
    <ul class="minerals">
      <li>Magnesium</li>
      <li>Natrium</li>
      <li>Kalcium</li>
      <li>Kalium</li>
    </ul>
    <svg class="emblem-ring" viewBox="0 0 450 450" aria-hidden="true">
      <circle cx="225" cy="225" r="220" fill="none" stroke="var(--ink-light)" stroke-width="3"/>
    </svg>
    <h1 class="brand brand-name">FLUXO4</h1>
    <p class="brand brand-tagline">Elektrolyt-Getränk</p>
    <p class="brand brand-flavour">Zitrone-Limette</p>
  </section>
</body>
</html>
```